Home Loan Introducer needs logo/business cards

We need a simple but classy logo for business cards and flyers. The business is a home loan referral business that is called an Introducer. The business name is "The Harborline".
I was thinking very simple and straight to the point on the front with "Home Loans" the only thing on the front with a nice background colour/s.
Then on the back, "The Harborline"
and "Quality Customer Service"
and "Email, text or call welcome"
and then my name, email address and phone number.
Updates
Thank you for all the designs :-)
Target Market(s)
Home buyers.
Home owners.
Investors.
Industry/Entity Type
Loan
Look and feel

```html
<!DOCTYPE html>
<html lang="en">
<head>
<meta charset="utf-8">
<title>The Harborline – Business Cards</title>
<link rel="stylesheet" href="https://fonts.googleapis.com/css2?family=Exo+2:wght@500;600;800&display=swap">
<style>
  :root {
    --stage: #ece8e3;
    --brand-blue: #0a67b0;
    --brand-orange: #fbac36;
    --paper: #ffffff;
    --shadow: rgba(40, 25, 10, 0.28);
  }
  * { box-sizing: border-box; margin: 0; padding: 0; }
  html, body { width: 1200px; height: 750px; overflow: hidden; }
  body {
    background: var(--stage);
    font-family: "Exo 2", "Trebuchet MS", sans-serif;
    position: relative;
  }
  .card {
    position: absolute;
    top: 215px;
    width: 520px;
    height: 320px;
    box-shadow: 0 10px 28px var(--shadow);
    overflow: hidden;
  }
  .card--front { left: 50px; background: var(--brand-blue); }
  .card--back  { left: 630px; background: var(--paper); }

  .front-band {
    position: absolute;
    left: 40px; right: 40px; top: 122px;
    height: 78px;
    background: var(--brand-orange);
    border-radius: 10px;
    display: flex; align-items: center; justify-content: center;
  }
  .front-title {
    color: var(--paper);
    font-weight: 800;
    font-size: 60px;
    letter-spacing: 1px;
    line-height: 1;
  }

  .back-lower {
    position: absolute;
    left: 0; right: 0; bottom: 0;
    height: 178px;
    background: var(--brand-orange);
  }
  .brand-name {
    position: absolute;
    top: 92px; left: 0; right: 0;
    display: flex; align-items: center; justify-content: center; gap: 12px;
    color: var(--brand-blue);
    font-weight: 800;
    font-size: 30px;
    text-transform: uppercase;
    letter-spacing: 1px;
  }
  .brand-square {
    width: 22px; height: 22px;
    background: var(--brand-orange);
  }
  .back-details {
    position: absolute;
    top: 160px; left: 0; right: 0;
    text-align: center;
    color: var(--brand-blue);
  }
  .service-list { list-style: none; font-weight: 600; font-size: 17px; line-height: 1.3; }
  .service-list li { display: flex; align-items: center; justify-content: center; gap: 6px; }
  .tick { width: 16px; height: 16px; }
  .tick path { fill: none; stroke: var(--paper); stroke-width: 3; stroke-linecap: round; stroke-linejoin: round; }
  .holder-name {
    margin-top: 12px;
    font-weight: 600; font-size: 22px;
  }
  .holder-rule {
    width: 240px; height: 2px; margin: 4px auto 6px;
    background: var(--paper);
  }
  .contact { font-size: 12px; font-weight: 500; line-height: 1.35; color: var(--brand-blue); }
  .contact span { color: var(--paper); }
</style>
</head>
<body>
  <section class="card card--front" aria-label="Card front">
    <div class="front-band">
      <h1 class="front-title">HOME LOAN</h1>
    </div>
  </section>

  <section class="card card--back" aria-label="Card back">
    <div class="back-lower"></div>
    <div class="brand-name"><span class="brand-square"></span>The Harborline</div>
    <div class="back-details">
      <ul class="service-list">
        <li><svg class="tick" viewBox="0 0 16 16"><path d="M2 9l4 4 8-10"/></svg>Quality Customer Service</li>
        <li><svg class="tick" viewBox="0 0 16 16"><path d="M2 9l4 4 8-10"/></svg>Email, text or call welcome</li>
      </ul>
      <p class="holder-name">Colin Marsh</p>
      <div class="holder-rule"></div>
      <p class="contact"><span>Phone:</span> +6305550142</p>
      <p class="contact"><span>Email:</span> colin@harborline.net</p>
    </div>
  </section>
</body>
</html>
```